Tutoring center for k-12 and adults. ( name: Birch Tutoring )

We will start a tutoring center mainly teaching international students English, math, test prep ( SAT,ACT) for K-12 and English conversation class and English grammar for adults. Our mission and description is well described in the attached file below.
Our center is located in Ann Arbor Michigan, and will provide highly qualified instructors.
Our motto is " school like a home and teacher like parents" and "Birch Tutoring is the passage to success" and "Learn to think" I want you to have these main themes as designing the website, and we already have a designed logo attached below in the file. As the name shows, greenish, fresh feeling, but academically informative design is strongly recommended.
I want to emphasize warm and caring atmosphere of our center with the images fitting to this concept.

Target Market(s)

international students (k-12) and adults for ESL classes / high school students both American and international students for test preps: ACT,SAT

Industry/Entity Type

Education

Coding

Number of Pages Required

3 page

Font styles to use
Serif
Sans Serif
Script

Requirements
Must have
• I think there are many options in my website to create different things, but at this point, I just want to make four headings on the top- Home, About us, Classes, Support.
• Home page includes mission statement, testimonial, brief introduction of Test prep classes (SAT,ACT), academic tutoring, and adults classes. Also logo and contact info should be located in the first page. As a second page (heading), classes need to be introduced. I wonder if I can insert Korean for Korean classes. In this section, I want to put class descriptions of each class. As a third heading, About us includes introduction of instructors with their educational background, and please make two more open spots for instructors because we will add more faculties later.
• As the last heading, Support is the section for Q &A and provide the address and map of the center. This part is optional if I go with 3 pages of website!
• It should be informative and simple, easy to find the necessary info.
• If I can update the info by semester or periodically by myself. If it's easy to aces to change and manage the info for me, it will be great.
Nice to have
• .
• If I can have an option to convert the language of the website from English to Korean or to Chinese, it will be very nice.
Should not have
• lesson fees

```html
<!DOCTYPE html>
<html lang="en">
<head>
<meta charset="utf-8">
<title>Birch Tutoring</title>
<link href="https://fonts.googleapis.com/css2?family=Roboto:wght@300;400;500;700&family=Roboto+Condensed:wght@300;400;700&display=swap" rel="stylesheet">
<style>
:root{
  --blue:#1d5ba8;
  --blue-dark:#174c8f;
  --green:#8bbd2c;
  --green-dark:#76a620;
  --grey-band:#ebebeb;
  --grey-light:#f3f3f3;
  --ink:#222;
  --body:#555;
  --muted:#888;
  --black:#111;
}
*{margin:0;padding:0;box-sizing:border-box}
html,body{width:1200px;height:2449px;overflow:hidden;background:#fff}
body{position:relative;font-family:'Roboto',Arial,sans-serif;color:var(--ink)}
.abs{position:absolute}

/* header */
.site-header{left:0;top:0;width:1200px;height:140px;background:#fff}
.brand{left:90px;top:40px;display:flex;align-items:center;gap:10px}
.brand-dot{width:46px;height:46px;border-radius:50%;background:var(--green)}
.brand-name{font-size:24px;font-weight:500;color:var(--blue)}
.btn-top{top:26px;height:33px;border-radius:3px;color:#fff;font-size:13px;display:flex;align-items:center;justify-content:center}
.btn-signin{left:740px;width:82px;background:var(--green)}
.btn-register{left:833px;width:83px;background:var(--blue)}
.lang-select{left:931px;top:26px;width:124px;height:33px;border:1px solid #ccc;border-radius:3px;font-size:13px;color:var(--blue);display:flex;align-items:center;justify-content:center;gap:8px}
.lang-flag{width:16px;height:11px;background:linear-gradient(#c33 0 50%,#fff 50% 100%);border:1px solid #ccc}
.search-btn{left:1076px;top:24px;width:38px;height:38px;border:1px solid #ddd;border-radius:3px;display:flex;align-items:center;justify-content:center}
.main-nav{left:0;top:87px;width:1200px;height:53px}
.nav-links{top:87px;height:53px;left:0;width:1200px;list-style:none}
.nav-links li{position:absolute;top:0;line-height:53px;color:#fff;font-size:11.5px;font-weight:400;letter-spacing:.2px;white-space:nowrap}

/* hero */
.hero{left:0;top:140px;width:1200px;height:613px;background:linear-gradient(180deg,#c9b48e 0%,#8a9a6a 45%,#7aa150 70%,#cfc7b9 100%)}
.hero-caption{left:90px;top:459px;width:392px;height:131px;background:rgba(60,60,60,.7);padding:22px 24px 0 23px}
.hero-title{font-family:'Roboto Condensed',Arial,sans-serif;font-size:41px;font-weight:400;color:#fff;line-height:1;white-space:nowrap;letter-spacing:-.3px}
.hero-sub{font-size:22px;color:#fff;font-weight:400;margin-top:12px;white-space:nowrap}
.hero-arrows{left:90px;top:619px;display:flex;gap:2px}
.hero-arrow{width:36px;height:41px;background:rgba(60,60,60,.7);border:1px solid rgba(255,255,255,.5);display:flex;align-items:center;justify-content:center}

/* services */
.services{left:0;top:753px;width:1200px;height:372px;background:var(--grey-band)}
.service{top:821px;width:300px;margin-left:-150px;text-align:center}
.service-icon{width:98px;height:98px;margin:0 auto;border-radius:50%;background:var(--green);border:5px solid #fff;box-shadow:0 0 0 1px #ddd;display:flex;align-items:center;justify-content:center}
.service-title{margin-top:26px;font-size:17px;font-weight:400;color:#222}
.service-text{margin-top:12px;font-size:12px;line-height:17px;color:#333}
.btn-more{display:inline-block;width:105px;height:33px;line-height:31px;margin-top:22px;background:#fff;border:1px solid #ccc;border-radius:3px;box-shadow:0 2px 2px rgba(0,0,0,.15);font-size:11px;color:#333}

/* welcome */
.welcome{left:0;top:1125px;width:1200px;height:235px;background:#fff;text-align:center}
.welcome-title{margin-top:44px;font-size:21px;font-weight:500;color:#222}
.welcome-title span{color:var(--blue)}
.welcome-text{width:922px;margin:16px auto 0;font-size:12.5px;line-height:22px;color:#666}
.btn-green{display:inline-block;width:105px;height:33px;line-height:33px;margin-top:22px;background:var(--green);border-radius:3px;color:#fff;font-size:12px;box-shadow:0 2px 2px rgba(0,0,0,.2)}

/* courses */
.courses{left:0;top:1360px;width:1200px;height:342px;background:linear-gradient(135deg,#eeeeee,#f6f6f6 50%,#ececec)}
.section-title{font-size:18px;font-weight:500;color:#222}
.section-title span{color:var(--blue)}
.courses-title{left:91px;top:1393px}
.courses-nav{left:1083px;top:1392px}
.course{top:1435px;width:249px}
.course-photo{width:249px;height:156px;border:3px solid #fff;box-shadow:0 0 0 1px #ddd}
.course-name{margin-top:23px;font-size:15px;color:#222}
.course-text{margin-top:8px;font-size:11px;line-height:17px;color:var(--muted)}

/* blog */
.blog-title{left:91px;top:1760px}
.post{left:91px;width:640px;display:flex;gap:15px}
.post-photo{width:185px;height:131px;flex:none}
.post-name{font-size:14px;color:#222;margin-top:2px}
.post-date{font-size:12px;color:var(--green);margin-top:12px}
.post-text{font-size:11px;line-height:19px;color:#444;margin-top:6px}

/* testimonials */
.testi-title{left:790px;top:1760px;font-weight:400}
.quote-box{left:792px;top:1819px;width:320px;height:167px;background:var(--green);border-radius:2px;padding:20px 22px;color:#fff;font-size:12.5px;line-height:23px}
.quote-mark{font-size:26px;font-weight:700;line-height:10px;vertical-align:-6px;margin-right:6px}
.avatar{left:813px;top:2004px;width:88px;height:88px;border-radius:50%;background:linear-gradient(#b99378,#6d5444);border:3px solid #fff;box-shadow:0 0 0 1px #ddd}
.author{left:919px;top:2014px;font-size:14px;color:#444;white-space:nowrap}
.author b{color:var(--blue);font-weight:400}
.testi-arrows{left:923px;top:2061px;display:flex;gap:6px}
.small-arrow{width:24px;height:24px;border:1px solid #ddd;display:flex;align-items:center;justify-content:center}

/* footer */
.site-footer{left:0;top:2149px;width:1200px;height:219px;background:var(--blue)}
.footer-col{top:2185px;color:#fff}
.footer-head{font-size:15px;font-weight:400;letter-spacing:.3px;margin-bottom:18px}
.footer-links{list-style:none;font-size:11px;line-height:24.5px}
.footer-links li::before{content:"";display:inline-block;border-left:5px solid #fff;border-top:3.5px solid transparent;border-bottom:3.5px solid transparent;margin-right:6px}
.footer-text{font-size:11px;line-height:19px}
.news-form{display:flex;margin-top:14px}
.news-input{width:147px;height:30px;background:#fff;color:#666;font-size:11px;line-height:30px;padding-left:12px}
.news-submit{width:55px;height:30px;background:var(--green);font-size:11px;line-height:30px;text-align:center}
.social{display:flex;gap:16px;margin-top:18px}
.social span{width:32px;height:32px;border-radius:50%;border:2px solid #fff}
.copyright-bar{left:0;top:2368px;width:1200px;height:81px;background:var(--black);color:#fff;font-size:11px;text-align:center;line-height:81px}
</style>
</head>
<body>

<header class="abs site-header">
  <div class="abs brand"><span class="brand-dot"></span><span class="brand-name">Birch Tutoring</span></div>
  <a class="abs btn-top btn-signin">SIGN IN</a>
  <a class="abs btn-top btn-register">REGISTER</a>
  <div class="abs lang-select"><span class="lang-flag"></span>ENGLISH
    <svg width="8" height="6" viewBox="0 0 8 6"><path d="M1 1l3 3 3-3" stroke="#1d5ba8" fill="none" stroke-width="1.5"/></svg></div>
  <div class="abs search-btn"><svg width="14" height="14" viewBox="0 0 14 14"><circle cx="6" cy="6" r="4.5" stroke="#666" stroke-width="1.5" fill="none"/><path d="M9.5 9.5L13 13" stroke="#666" stroke-width="1.5"/></svg></div>
</header>

<svg class="abs main-nav" viewBox="0 0 1200 53" width="1200" height="53"><polygon points="269,0 1200,0 1200,53 240,53" fill="#1d5ba8"/><polygon points="269,0 1200,0 1200,4 266,4" fill="#174c8f"/></svg>
<ul class="abs nav-links">
  <li style="left:294px">HOME</li>
  <li style="left:361px">MISSION STATEMENT</li>
  <li style="left:509px">CLASSES INSTRUCTORS</li>
  <li style="left:671px">LOCATION</li>
  <li style="left:761px">TESTIMONIALS</li>
  <li style="left:879px">ACADEMIC PICTURES</li>
  <li style="left:1027px">CONTACT US</li>
</ul>

<section class="abs hero" role="img" aria-label="Photo of five smiling schoolchildren with backpacks running toward the camera outside a school"></section>
<div class="abs hero-caption">
  <div class="hero-title">SCHOOL LIKE A HOME</div>
  <div class="hero-sub">AND TEACHER LIKE PARENTS</div>
</div>
<div class="abs hero-arrows">
  <span class="hero-arrow"><svg width="10" height="18" viewBox="0 0 10 18"><path d="M9 1L1 9l8 8" stroke="#fff" fill="none" stroke-width="1.5"/></svg></span>
  <span class="hero-arrow"><svg width="10" height="18" viewBox="0 0 10 18"><path d="M1 1l8 8-8 8" stroke="#fff" fill="none" stroke-width="1.5"/></svg></span>
</div>

<section class="abs services"></section>
<div class="abs service" style="left:238px">
  <div class="service-icon"><svg width="36" height="34" viewBox="0 0 36 34" fill="#fff"><polygon points="18,0 36,9 0,9"/><rect x="2" y="11" width="32" height="3"/><rect x="5" y="15" width="4" height="13"/><rect x="13" y="15" width="4" height="13"/><rect x="21" y="15" width="4" height="13"/><rect x="29" y="15" width="4" height="13"/><rect x="0" y="29" width="36" height="4"/></svg></div>
  <div class="service-title">SAT / ACT</div>
  <p class="service-text">Lorem Ipsum has been the industry's standard<br>dummy text ever since the 1500s, when an</p>
  <a class="btn-more">Read More</a>
</div>
<div class="abs service" style="left:594px">
  <div class="service-icon"><svg width="32" height="32" viewBox="0 0 32 32"><circle cx="16" cy="16" r="14" fill="#fff"/><path d="M9 9c4 1 5 4 3 7s2 5 0 8M20 6c-2 3 1 5 4 5s2 4 1 7" stroke="#8bbd2c" stroke-width="3" fill="none"/></svg></div>
  <div class="service-title">ACADEMIC TUTORING</div>
  <p class="service-text">Lorem Ipsum has been the industry's standard<br>dummy text ever since the 1500s, when an</p>
  <a class="btn-more">Read More</a>
</div>
<div class="abs service" style="left:942px">
  <div class="service-icon"><svg width="40" height="30" viewBox="0 0 40 30" fill="#fff"><circle cx="20" cy="7" r="6"/><path d="M10 28c0-8 4-12 10-12s10 4 10 12z"/><circle cx="7" cy="11" r="4"/><path d="M0 26c0-6 3-9 7-9 2 0 3 1 4 2-2 2-3 4-3 7z"/><circle cx="33" cy="11" r="4"/><path d="M40 26c0-6-3-9-7-9-2 0-3 1-4 2 2 2 3 4 3 7z"/></svg></div>
  <div class="service-title" style="color:#555">ADULT CLASS</div>
  <p class="service-text">Lorem Ipsum has been the industry's standard<br>dummy text ever since the 1500s, when an</p>
  <a class="btn-more">Read More</a>
</div>

<section class="abs welcome">
  <h2 class="welcome-title">WELCOME TO <span>BIRCH TUTORING</span></h2>
  <p class="welcome-text">Lorem Ipsum has been the industry's standard dummy text ever since the 1500s, when an unknown printer took a galley of type and scrambled it to make a type specimen book. It has survived not only five centuries, but also the leap into electronic typesetting, remaining essentially unchanged. It was popularised in the 1960s with the release of Letraset sheets containing Lorem Ipsum passages, and more recently with desktop publishing software</p>
  <a class="btn-green">Read More</a>
</section>

<section class="abs courses"></section>
<h2 class="abs section-title courses-title">POPULAR <span>COURSES</span></h2>
<svg class="abs courses-nav" width="28" height="20" viewBox="0 0 28 20"><path d="M9 2L2 10l7 8M19 2l7 8-7 8" stroke="#222" stroke-width="2" fill="none"/></svg>
<div class="abs course" style="left:91px">
  <div class="course-photo" role="img" aria-label="Photo of pupils raising hands in a classroom" style="background:linear-gradient(#4f6b4a,#8a7560)"></div>
  <div class="course-name">Basic Cooking Techniques</div>
  <p class="course-text">Lorem Ipsum has been the industry's standard dummy text ever since the 1500s,</p>
</div>
<div class="abs course" style="left:351px">
  <div class="course-photo" role="img" aria-label="Photo of smiling children drawing together at a table" style="background:linear-gradient(#4c83c4,#e0b35a)"></div>
  <div class="course-name">Home Fitness Training</div>
  <p class="course-text">Lorem Ipsum has been the industry's standard dummy text ever since the 1500s,</p>
</div>
<div class="abs course" style="left:607px">
  <div class="course-photo" role="img" aria-label="Photo of schoolchildren with backpacks in a school hallway" style="background:linear-gradient(#b8a48e,#a5566a)"></div>
  <div class="course-name">Digital Photography</div>
  <p class="course-text">Lorem Ipsum has been the industry's standard dummy text ever since the 1500s,</p>
</div>
<div class="abs course" style="left:866px">
  <div class="course-photo" role="img" aria-label="Photo of two pupils writing at their desks" style="background:linear-gradient(#d9d3c2,#8a9fc0)"></div>
  <div class="course-name">Architecture Basics</div>
  <p class="course-text">Lorem Ipsum has been the industry's standard dummy text ever since the 1500s,</p>
</div>

<h2 class="abs section-title blog-title">LATEST <span>BLOG</span></h2>
<article class="abs post" style="top:1811px">
  <div class="post-photo" role="img" aria-label="Photo of a boy reading a book" style="background:linear-gradient(135deg,#8fa7b8,#6b5a48)"></div>
  <div><h3 class="post-name" style="font-weight:400">Nemo Enim Ipsam Volup</h3><div class="post-date">09-07-2015</div>
  <p class="post-text">Lorem Ipsum has been the industry's standard dummy text ever since the 1500s, when an unknown printer took a galley of type and scrambled it to make a type specimen book. It has survived not only five centuries,</p></div>
</article>
<article class="abs post" style="top:1958px">
  <div class="post-photo" role="img" aria-label="Photo of an open book on a desk" style="background:linear-gradient(#5b6fa0,#c9c3c8 55%,#6a4a2e)"></div>
  <div><h3 class="post-name" style="font-weight:400">Nemo Enim Ipsam Volup</h3><div class="post-date">09-07-2015</div>
  <p class="post-text">Lorem Ipsum has been the industry's standard dummy text ever since the 1500s, when an unknown printer took a galley of type and scrambled it to make a type specimen book. It has survived not only five centuries,</p></div>
</article>

<h2 class="abs section-title testi-title">TESTIMONIALS</h2>
<blockquote class="abs quote-box"><span class="quote-mark">&ldquo;</span>Lorem ipsum dolor sit amet, consectetur adipiscing elit, sed do eiusmod tempor incididunt ut labore et dolore magna aliqua. Ut enim ad minim veniam, quis nostrud exercitation Lorem ipsum dolor sit amet,</blockquote>
<svg class="abs" style="left:1012px;top:1985px" width="34" height="24" viewBox="0 0 34 24"><polygon points="0,0 34,0 32,24" fill="#8bbd2c"/></svg>
<div class="abs avatar" role="img" aria-label="Portrait of the reviewer"></div>
<div class="abs author"><b>Dana Whitfield</b> - &nbsp;Parents Education</div>
<div class="abs testi-arrows">
  <span class="small-arrow"><svg width="6" height="10" viewBox="0 0 6 10"><path d="M5 1L1 5l4 4" stroke="#333" fill="none" stroke-width="1.5"/></svg></span>
  <span class="small-arrow"><svg width="6" height="10" viewBox="0 0 6 10"><path d="M1 1l4 4-4 4" stroke="#333" fill="none" stroke-width="1.5"/></svg></span>
</div>

<footer class="abs site-footer"></footer>
<div class="abs footer-col" style="left:91px">
  <h4 class="footer-head">LINKS</h4>
  <ul class="footer-links"><li>Customer Support</li><li>Documentation</li><li>Resources</li><li>General FAQs</li><li>Shortcodes</li></ul>
</div>
<div class="abs footer-col" style="left:304px;width:230px">
  <h4 class="footer-head">TOP EXPERTS</h4>
  <p class="footer-text">&nbsp;Lorem Ipsum has been the industry's standard dummy text ever since the 1500s, when an unknown printer took</p>
  <p class="footer-text" style="margin-top:4px">a galley of type and scrambled it to make a type specimen book. It has survived not only five centuries, but also the leap into electronic</p>
</div>
<div class="abs footer-col" style="left:655px;width:200px">
  <h4 class="footer-head">GET IN TOUCH</h4>
  <p class="footer-text">Address : 742 Maple Grove Rd,<br>Ann Arbor, MI</p>
  <p class="footer-text" style="margin-top:18px">Phone : 734 555 0198</p>
  <p class="footer-text" style="margin-top:18px">Email : hello@birchtutoring.edu</p>
</div>
<div class="abs footer-col" style="left:910px;width:210px">
  <h4 class="footer-head">NEWSLETTER</h4>
  <p class="footer-text">Your about us information would fit<br>here nicely.</p>
  <div class="news-form"><span class="news-input">Email address</span><span class="news-submit">Submit</span></div>
  <div class="social"><span aria-label="Social link"></span><span aria-label="Social link"></span><span aria-label="Social link"></span></div>
</div>
<div class="abs copyright-bar">Copyright &copy; 2015. All Rights Reserved</div>

</body>
</html>
```